Heron Loan Partners Business Card

We need a business card design for our mortgage servicing company. In addition to servicing the loans of homeowners, we help homeowners with purchasing their homes and any mortgage refinancing. We would like to see designs that use the colors in the logo attached below (gold-ish yellow and navy blue), and any other design you deem fit! The design should communicate a simpler life with smart mortgages provided by Heron.

```html
<!DOCTYPE html>
<html lang="en">
<head>
<meta charset="UTF-8">
<title>Heron Loan Partners Business Card</title>
<link href="https://fonts.googleapis.com/css2?family=Montserrat:wght@400;500;700;800&display=swap" rel="stylesheet">
<style>
  :root {
    --gold: #e0b33f;
    --navy: #26215a;
    --white: #ffffff;
    --ink: #1d1d1f;
    --backdrop: #2a2a2c;
  }
  * { box-sizing: border-box; margin: 0; padding: 0; }
  html, body { width: 1200px; height: 880px; overflow: hidden; }
  body {
    background: var(--backdrop);
    font-family: "Montserrat", sans-serif;
    position: relative;
  }
  .card {
    position: absolute;
    width: 540px;
    height: 309px;
    overflow: hidden;
    box-shadow: 0 10px 30px rgba(0,0,0,0.45);
  }
  .card--front {
    left: 50px;
    top: 170px;
    background: var(--gold);
    display: flex;
    align-items: center;
    justify-content: center;
  }
  .wordmark {
    font-weight: 800;
    letter-spacing: 0.5px;
    display: flex;
    align-items: center;
    gap: 12px;
    white-space: nowrap;
  }
  .wordmark__dot {
    border-radius: 50%;
    flex: none;
  }
  .card--front .wordmark { color: var(--white); font-size: 34px; }
  .card--front .wordmark__dot { width: 22px; height: 22px; background: var(--white); }

  .card--back {
    left: 610px;
    top: 400px;
    background: var(--white);
  }
  .card--back .wordmark {
    position: absolute;
    left: 250px;
    top: 36px;
    color: var(--gold);
    font-size: 20px;
    gap: 8px;
    z-index: 1;
  }
  .card--back .wordmark__dot { width: 14px; height: 14px; background: var(--navy); }
  .wave { position: absolute; inset: 0; }
  .holder {
    position: absolute;
    left: 32px;
    top: 108px;
    z-index: 1;
  }
  .holder__name {
    font-weight: 800;
    font-size: 15px;
    color: var(--navy);
    letter-spacing: 0.3px;
  }
  .holder__name span { color: var(--gold); }
  .holder__role {
    font-size: 13px;
    color: var(--ink);
    margin-top: 2px;
  }
  .contact {
    position: absolute;
    left: 32px;
    top: 174px;
    list-style: none;
    z-index: 1;
  }
  .contact li {
    display: flex;
    align-items: center;
    gap: 10px;
    font-size: 12.5px;
    color: var(--ink);
    line-height: 21px;
  }
  .contact svg { width: 13px; height: 13px; flex: none; }
  .address {
    position: absolute;
    right: 30px;
    top: 80px;
    font-size: 12.5px;
    color: var(--ink);
    text-align: left;
    line-height: 18px;
    z-index: 1;
  }
</style>
</head>
<body>
  <section class="card card--front" aria-label="Card front">
    <div class="wordmark"><span class="wordmark__dot"></span>Heron Loan Partners</div>
  </section>

  <section class="card card--back" aria-label="Card back">
    <svg class="wave" viewBox="0 0 540 309" preserveAspectRatio="none" aria-hidden="true">
      <path d="M0 300 C 200 296, 305 264, 375 205 S 485 143, 540 137 L540 309 L0 309 Z" fill="var(--gold)"/>
      <path d="M0 292 C 200 288, 300 255, 370 195 S 480 135, 540 128" fill="none" stroke="var(--navy)" stroke-width="5"/>
    </svg>

    <div class="wordmark"><span class="wordmark__dot"></span>Heron Loan Partners</div>

    <div class="holder">
      <p class="holder__name">DANA <span>WHITFIELD</span></p>
      <p class="holder__role">Owner</p>
    </div>

    <p class="address">482 Willow Crest Ave, Ste<br>210, Dallas, TX 75219</p>

    <ul class="contact">
      <li>
        <svg viewBox="0 0 16 16" aria-hidden="true"><path d="M3 2h3l1.5 3.5-2 1.2a8 8 0 0 0 3.8 3.8l1.2-2L14 10v3a1 1 0 0 1-1 1A12 12 0 0 1 2 3a1 1 0 0 1 1-1z" fill="var(--gold)"/></svg>
        555.014.2290
      </li>
      <li>
        <svg viewBox="0 0 16 16" aria-hidden="true"><rect x="1" y="3" width="14" height="10" rx="1" fill="var(--gold)"/><path d="M1.5 3.5 8 9l6.5-5.5" fill="none" stroke="var(--white)" stroke-width="1.3"/></svg>
        info@heronloanpartners.com
      </li>
      <li>
        <svg viewBox="0 0 16 16" aria-hidden="true"><circle cx="8" cy="8" r="7" fill="var(--gold)"/><path d="M1 8h14M8 1c2.5 2.5 2.5 11.5 0 14M8 1c-2.5 2.5-2.5 11.5 0 14" fill="none" stroke="var(--white)" stroke-width="1"/></svg>
        www.heronloanpartners.com
      </li>
    </ul>
  </section>
</body>
</html>
```